Harbourline Electrical Solutions

On one side. LOGO (underneath:) Commercial Industrial Residential

- NAME & CONTACT DETAILS

Marcus T. Hollings
Project Manager

(Cell icon) (441) 555-0187
(Email icon) hlelectricalsolutions@mailvento.com
(Facebook & Instagram icons )@hlelectricalsolutions

Other side: LOGO - underneath ELECTRICAL CONSTRUCTION & MAINTENANCE . LED LIGHTING & AUTOMATION . LIFE SAFETY SYSTEMS (FIRE ALARM / SECURITY) . DATA & COMMUNICATION

```html
<!DOCTYPE html>
<html lang="en">
<head>
<meta charset="utf-8">
<title>Harbourline Electrical Solutions – Business Card</title>
<link href="https://fonts.googleapis.com/css2?family=Montserrat:wght@400;500;600;700&display=swap" rel="stylesheet">
<style>
  :root {
    --stage: #8d8d8d;
    --charcoal: #4b4b4d;
    --charcoal-ink: #2c2c2e;
    --teal: #1c6b80;
    --teal-deep: #155a6c;
    --swoosh: #5a5a5c;
    --paper: #ffffff;
    --ink: #2f3a40;
    --on-teal: #ffffff;
  }
  * { box-sizing: border-box; margin: 0; padding: 0; }
  html, body { width: 1200px; height: 960px; overflow: hidden; }
  body {
    background: var(--stage);
    font-family: "Montserrat", sans-serif;
    display: flex;
    flex-direction: column;
    align-items: center;
    justify-content: center;
    gap: 40px;
  }
  .card {
    position: relative;
    width: 700px;
    height: 400px;
    border-radius: 24px;
    overflow: hidden;
  }

  /* Back side */
  .card--back {
    background: var(--charcoal);
    color: var(--charcoal-ink);
  }
  .card--back .brand {
    position: absolute;
    left: 150px;
    top: 120px;
    display: flex;
    align-items: center;
    gap: 16px;
  }
  .brand-mark {
    width: 22px;
    height: 22px;
    background: currentColor;
  }
  .brand-name {
    font-weight: 600;
    font-size: 26px;
    line-height: 1.12;
    letter-spacing: 3px;
    text-transform: uppercase;
  }
  .services {
    position: absolute;
    left: 90px;
    top: 262px;
    font-size: 14px;
    font-weight: 500;
    line-height: 1.6;
    white-space: nowrap;
  }

  /* Front side */
  .card--front { background: var(--paper); }
  .card-shapes { position: absolute; inset: 0; }
  .card--front .brand {
    position: absolute;
    left: 40px;
    top: 62px;
    color: var(--teal-deep);
    display: flex;
    align-items: center;
    gap: 12px;
  }
  .card--front .brand-name { font-size: 20px; letter-spacing: 2px; }
  .card--front .brand-mark { width: 16px; height: 16px; }
  .sectors {
    position: absolute;
    left: 40px;
    top: 140px;
    font-size: 11.5px;
    font-weight: 500;
    letter-spacing: 0.5px;
    color: var(--ink);
    white-space: nowrap;
  }
  .contact {
    position: absolute;
    right: 34px;
    top: 150px;
    text-align: right;
    color: var(--on-teal);
  }
  .contact-name {
    font-size: 20px;
    font-weight: 700;
    letter-spacing: 0.5px;
    text-transform: uppercase;
    white-space: nowrap;
  }
  .contact-role {
    font-size: 13px;
    font-weight: 500;
    margin-bottom: 16px;
  }
  .contact-list { list-style: none; }
  .contact-list li {
    display: flex;
    justify-content: flex-end;
    align-items: center;
    gap: 8px;
    font-size: 12px;
    line-height: 1.75;
    white-space: nowrap;
  }
  .icon { width: 13px; height: 13px; flex: none; }
</style>
</head>
<body>

  <section class="card card--back" aria-label="Card back">
    <div class="brand">
      <span class="brand-mark"></span>
      <span class="brand-name">Harbourline<br>Electrical<br>Solutions</span>
    </div>
    <p class="services">
      Electrical Construction &amp; Maintenance • LED Lighting &amp; Automation<br>
      Life Safety Systems (Fire Alarm / Security) • Data &amp; Communication
    </p>
  </section>

  <section class="card card--front" aria-label="Card front">
    <svg class="card-shapes" viewBox="0 0 700 400" aria-hidden="true">
      <path d="M300 0 C370 110 360 290 230 400 L252 400 C382 290 392 110 322 0 Z" fill="var(--swoosh)"/>
      <path d="M322 0 H700 V400 H252 C382 290 392 110 322 0 Z" fill="var(--teal)"/>
    </svg>

    <div class="brand">
      <span class="brand-mark"></span>
      <span class="brand-name">Harbourline<br>Electrical<br>Solutions</span>
    </div>
    <p class="sectors">COMMERCIAL • INDUSTRIAL • RESIDENTIAL</p>

    <div class="contact">
      <p class="contact-name">Marcus T. Hollings</p>
      <p class="contact-role">Project Manager</p>
      <ul class="contact-list">
        <li>(441) 555-0187
          <svg class="icon" viewBox="0 0 13 13"><rect x="3" y="0.8" width="7" height="11.4" rx="1.3" fill="none" stroke="currentColor" stroke-width="1.3"/><circle cx="6.5" cy="10" r="0.8" fill="currentColor"/></svg>
        </li>
        <li>hlelectricalsolutions@mailvento.com
          <svg class="icon" viewBox="0 0 13 13"><rect x="0.8" y="2.5" width="11.4" height="8" fill="currentColor"/><path d="M1 3 L6.5 7 L12 3" fill="none" stroke="var(--teal)" stroke-width="1.2"/></svg>
        </li>
        <li>@hlelectricalsolutions
          <svg class="icon" viewBox="0 0 13 13"><circle cx="6.5" cy="6.5" r="6" fill="currentColor"/></svg>
        </li>
        <li>@hlelectricalsolutions
          <svg class="icon" viewBox="0 0 13 13"><circle cx="6.5" cy="6.5" r="6" fill="currentColor"/></svg>
        </li>
      </ul>
    </div>
  </section>

</body>
</html>
```